VORTEQ

It’s is a startup business. We design and build new products.

Target Market(s)

For my first two products, they are targeting the laundry market, hanger accessory, and new modern style clothes dryer. I also have a Pet Treat product at patent stage, and there are other products not yet started but will be more engineering based. Therefore from young adults to older population

Industry/Entity Type

Colours of website to match the logo (att)

Coding

Coded - Design and coding required

Number of Pages Required

1 page

Font styles to use
Other font styles liked:
• Some of the same font as the logo

Colors

Designer to choose colors to be used in the design.

Requirements
Must have
• An upbeat vibe - the logo looks great so inline with that !
Should not have
• anything old fashioned and old style fonts

```html
<!DOCTYPE html>
<html lang="en">
<head>
<meta charset="utf-8">
<title>VORTEQ — Innovation &amp; Technical Services</title>
<link href="https://fonts.googleapis.com/css2?family=Michroma&family=Roboto:wght@400;500;700&display=swap" rel="stylesheet">
<style>
:root{
  --teal:#0f9e97;
  --teal-dark:#0a7f7b;
  --teal-light:#1fc2b5;
  --navy:#2b2f86;
  --navy-deep:#1d2066;
  --cyan:#00a9dc;
  --ink:#0b0d2e;
  --ink-deep:#07081f;
  --text:#222;
  --muted:#666;
  --pale:#f4f5fb;
  --white:#fff;
}
*{box-sizing:border-box;margin:0;padding:0}
html,body{width:1200px;height:4278px;overflow:hidden}
body{position:relative;font-family:"Roboto",sans-serif;color:var(--text);background:var(--white)}
.abs{position:absolute}
.display{font-family:"Michroma",sans-serif;text-transform:uppercase;letter-spacing:2px;font-weight:400}
.btn{position:absolute;display:flex;align-items:center;justify-content:center;gap:8px;border-radius:30px;
  background:linear-gradient(90deg,var(--teal-dark),var(--teal-light));color:var(--white);font-weight:700;
  font-size:15px;letter-spacing:.5px;text-transform:uppercase;box-shadow:0 3px 8px rgba(0,0,0,.2)}

/* header */
.site-header{position:absolute;top:0;left:0;width:1200px;height:83px;background:var(--white);z-index:3}
.brand{position:absolute;display:flex;align-items:center;gap:12px}
.brand-dot{width:34px;height:34px;border-radius:50%;background:var(--teal)}
.brand-name{font-family:"Michroma",sans-serif;font-size:26px;color:var(--navy);letter-spacing:3px}
.nav{position:absolute;left:510px;top:30px;display:flex;gap:26px;font-size:15px;color:#333}
.nav .active{color:var(--cyan)}

/* hero */
.hero{position:absolute;top:83px;left:0;width:1200px;height:662px}
.hero-title{position:absolute;top:75px;left:0;width:1200px;text-align:center;color:var(--white);line-height:1.35}
.hero-title .small{font-size:26px;letter-spacing:6px}
.hero-title .big{font-size:36px;letter-spacing:5px}

/* about */
.about-visual{position:absolute;left:110px;top:728px;width:465px;height:577px;border-radius:40% 10% 40% 10%;
  background:linear-gradient(135deg,var(--teal-light),#1a7fc4 50%,var(--navy-deep))}
.section-title{font-family:"Michroma",sans-serif;text-transform:uppercase;color:#1a1a1a;letter-spacing:3px}
.about-text{position:absolute;left:652px;top:820px;width:440px}
.about-text h3{font-size:16px;font-weight:500;line-height:1.5;margin:40px 0 18px}
.about-text p{font-size:13.5px;line-height:1.78;color:var(--muted);margin-bottom:14px}

/* solutions */
.solution{position:absolute;top:1335px;width:600px;height:605px;color:var(--white);text-align:center}
.solution .icon{position:absolute;left:255px;top:140px;width:90px;height:88px;border:3px solid rgba(255,255,255,.85);border-radius:12px}
.solution h2{position:absolute;top:262px;left:0;width:600px;font-size:18px;letter-spacing:3px}
.solution .rule{position:absolute;top:295px;left:270px;width:60px;height:3px;background:var(--white)}
.solution p{position:absolute;top:322px;left:110px;width:380px;font-size:14px;line-height:1.6}

/* why choose */
.why-title{position:absolute;left:110px;top:2030px;font-size:27px;line-height:1.6}
.why-item{position:absolute;left:110px;width:430px}
.why-item .badge{position:absolute;left:0;top:0;width:64px;height:64px;border-radius:50%;border:3px solid #fff;box-shadow:0 0 0 2px rgba(0,0,0,.08)}
.why-item h4{position:absolute;left:80px;top:8px;font-size:17px;font-weight:500}
.why-item p{position:absolute;left:80px;top:36px;font-size:13.5px;color:var(--muted);line-height:1.6;width:360px}
.why-visual{position:absolute;left:611px;top:1997px;width:477px;height:445px;
  background:radial-gradient(circle at 55% 35%,#f3d7c2 0,#5b7fb6 18%,#1a3a74 45%,#0a1530 100%)}

/* blog */
.blog-title{position:absolute;top:2610px;left:0;width:1200px;text-align:center;font-size:27px}
.post{position:absolute;top:2684px;width:312px;height:365px}
.post .thumb{position:absolute;top:0;left:0;width:312px;height:219px}
.post .card{position:absolute;top:166px;left:0;width:290px;height:197px;background:var(--white);box-shadow:0 4px 14px rgba(0,0,0,.06);padding:30px 30px}
.post .meta{font-size:12.5px;color:var(--navy);margin-bottom:10px}
.post h3{font-size:17px;font-weight:500;line-height:1.5;margin-bottom:12px;color:#111}
.post p{font-size:13px;color:var(--muted);line-height:1.7}
.post.featured .card{border-bottom:4px solid var(--teal)}

/* contact */
.contact-panel{position:absolute;left:108px;top:3233px;width:448px;height:385px;background:linear-gradient(160deg,var(--teal),var(--teal-dark))}
.contact-heading{position:absolute;left:120px;top:3338px;width:298px;text-align:right;color:var(--white)}
.contact-heading .eyebrow{font-size:18px;font-weight:700}
.contact-heading .headline{font-size:23px;line-height:1.85;margin-top:10px;letter-spacing:2px}
.contact-frame{position:absolute;left:741px;top:3253px;width:366px;height:345px;border:3px solid var(--navy-deep)}
.form-card{position:absolute;left:462px;top:3283px;width:625px;height:442px;background:var(--white);box-shadow:0 6px 28px rgba(0,0,0,.1);padding:40px 57px}
.form-card .section-title{font-size:22px}
.form-card .rule{width:58px;height:3px;background:var(--teal);margin:10px 0 0}
.field{position:absolute;width:228px}
.field label{display:block;font-size:14px;font-weight:500;color:#222;margin-bottom:12px}
.field span{display:block;font-size:12px;color:#888;padding-bottom:14px;border-bottom:1px solid #ccc}
.field.wide{width:430px}
.send{position:absolute;left:500px;top:325px;width:64px;height:64px;border-radius:50%;background:linear-gradient(135deg,var(--teal-light),var(--teal-dark));display:flex;align-items:center;justify-content:center}

/* footer */
.footer-shape{position:absolute;top:3820px;left:0}
.footer-brand{position:absolute;left:110px;top:4070px}
.footer-col{position:absolute;top:3965px;color:var(--white)}
.footer-col h5{font-size:17px;font-weight:700;margin-bottom:14px}
.footer-col .rule{width:58px;height:3px;background:var(--cyan);margin-bottom:24px}
.links li{list-style:none;font-size:12px;margin-bottom:14px}
.contact-line{display:flex;align-items:flex-start;gap:10px;font-size:12px;margin-bottom:18px;line-height:1.5}
.contact-line .ic{flex:none;width:24px;height:24px;border-radius:50%;background:var(--white);display:flex;align-items:center;justify-content:center}
.subscribe p{font-size:12px;line-height:1.7;width:250px;margin-bottom:16px}
.sub-form{display:flex;width:252px;height:34px;border-radius:4px;overflow:hidden}
.sub-form .input{flex:1;background:var(--white);color:#888;font-size:11px;display:flex;align-items:center;padding-left:12px}
.sub-form .go{width:46px;background:var(--teal);display:flex;align-items:center;justify-content:center}
.socials{display:flex;gap:12px;margin-top:20px}
.socials span{width:30px;height:30px;border-radius:50%;background:var(--white)}
.socials span.on{background:var(--cyan)}
.bottom-bar{position:absolute;left:0;top:4215px;width:1200px;height:63px;background:var(--ink-deep);color:var(--white);font-size:13px}
.bottom-bar .copy{position:absolute;left:110px;top:24px}
.bottom-bar .copy b{text-decoration:underline;font-weight:700}
.bottom-bar .legal{position:absolute;right:110px;top:24px}
</style>
</head>
<body>

<header class="site-header">
  <div class="brand" style="left:110px;top:22px">
    <span class="brand-dot"></span><span class="brand-name">VORTEQ</span>
  </div>
  <nav class="nav">
    <span class="active">Home</span><span>About Us</span><span>Products</span><span>Blog</span><span>Contact Us</span>
  </nav>
  <a class="btn" style="left:928px;top:20px;width:160px;height:42px;text-transform:none;font-size:15px">Explore Products</a>
</header>

<section class="hero">
  <svg width="1200" height="662" viewBox="0 0 1200 662" role="img" aria-label="Night-sky field of glowing purple and blue light streaks over a digital wave">
    <defs>
      <linearGradient id="heroSky" x1="0" y1="0" x2="0" y2="1">
        <stop offset="0" stop-color="#0a0b2c"/>
        <stop offset=".55" stop-color="#1c1556"/>
        <stop offset=".85" stop-color="#5a2a86"/>
        <stop offset="1" stop-color="#2a1a5e"/>
      </linearGradient>
    </defs>
    <polygon points="0,0 1200,0 1200,500 1097,530 600,640 103,530 0,500" fill="url(#heroSky)"/>
    <polygon points="103,530 600,640 1097,530 1097,552 600,662 103,552" fill="var(--cyan)"/>
  </svg>
  <div class="hero-title display">
    <div class="small">VORTEQ</div>
    <div class="big">Innovation &amp;</div>
    <div class="big">Technical Services</div>
  </div>
  <a class="btn" style="left:511px;top:253px;width:179px;height:47px;font-size:16px">Contact Us</a>
</section>

<section class="about">
  <div class="about-visual" role="img" aria-label="Abstract 3D ribbon shape in teal, cyan and deep blue"></div>
  <div class="about-text">
    <h2 class="section-title" style="font-size:28px">About Us</h2>
    <h3>Innovating Everyday Essentials – Smart Design,<br>Smart Living</h3>
    <p>At Vorteq, we believe that the best products are those that seamlessly blend functionality, modern aesthetics, and intelligent design. We are a product innovation company dedicated to reimagining the everyday – from laundry accessories to pet care solutions and beyond.</p>
    <p>To design and build smarter products that simplify daily life, offering practical solutions with engineering precision and contemporary style.</p>
  </div>
  <a class="btn" style="left:652px;top:1190px;width:186px;height:50px;font-size:15px">Learn More
    <svg width="14" height="14" viewBox="0 0 14 14"><circle cx="7" cy="7" r="7" fill="#fff"/><path d="M5.5 4l3 3-3 3" stroke="#0a7f7b" stroke-width="1.8" fill="none"/></svg>
  </a>
</section>

<svg class="abs" style="left:0;top:1335px" width="1200" height="605" viewBox="0 0 1200 605" aria-hidden="true">
  <defs>
    <linearGradient id="navyPanel" x1="0" y1="0" x2="0" y2="1"><stop offset="0" stop-color="#3a44a8"/><stop offset="1" stop-color="#23287a"/></linearGradient>
    <linearGradient id="cyanPanel" x1="0" y1="0" x2="0" y2="1"><stop offset="0" stop-color="#0aa6dc"/><stop offset="1" stop-color="#0d8fcc"/></linearGradient>
  </defs>
  <polygon points="0,0 600,70 600,535 0,605" fill="url(#navyPanel)"/>
  <polygon points="600,70 1200,0 1200,605 600,535" fill="url(#cyanPanel)"/>
</svg>

<div class="solution" style="left:0">
  <div class="icon" role="img" aria-label="Line icon of a washing machine"></div>
  <h2 class="display">Laundry Solutions</h2>
  <div class="rule"></div>
  <p>A sleek, efficient, and space-saving drying solution. This next-generation clothes dryer is designed for modern homes, combining style with smart drying technology.</p>
  <a class="btn" style="top:418px;left:219px;width:154px;height:44px">Learn More</a>
</div>
<div class="solution" style="left:600px">
  <div class="icon" role="img" aria-label="Line icon of a dog and a cat"></div>
  <h2 class="display">Pet Innovations</h2>
  <div class="rule"></div>
  <p>A game-changing treat innovation is on the way! Currently in the patent stage, this product is designed to provide healthier, more convenient treat options for pets.</p>
  <a class="btn" style="top:418px;left:230px;width:154px;height:44px">Learn More</a>
</div>

<section class="why">
  <h2 class="section-title why-title">Why Choose<br>Vorteq?</h2>
  <div class="why-item" style="top:2155px">
    <div class="badge" role="img" aria-label="Engineering gear icon" style="background:linear-gradient(135deg,#3a44a8,#1d2066)"></div>
    <h4>Innovative Engineering</h4>
    <p>Every product is designed with functionality &amp; modern aesthetics.</p>
  </div>
  <div class="why-item" style="top:2247px">
    <div class="badge" role="img" aria-label="Users icon" style="background:linear-gradient(135deg,#19c1e8,#0a8fc6)"></div>
    <h4>User-Focused Solutions</h4>
    <p>We solve real-life problems with practical designs.</p>
  </div>
  <div class="why-item" style="top:2336px">
    <div class="badge" role="img" aria-label="Leaf and globe icon" style="background:linear-gradient(135deg,#1fc2b5,#0a7f7b)"></div>
    <h4>Sustainable &amp; Efficient</h4>
    <p>Thoughtful materials and energy-saving features.</p>
  </div>
  <div class="why-visual" role="img" aria-label="Robotic hand and human hand reaching toward a glowing light bulb"></div>
</section>

<section class="blog">
  <svg class="abs" style="left:0;top:2525px" width="1200" height="615" viewBox="0 0 1200 615" aria-hidden="true">
    <polygon points="0,50 600,0 1200,50 1200,615 0,615" fill="var(--pale)"/>
  </svg>
  <h2 class="section-title blog-title">Our Blog</h2>

  <article class="post" style="left:112px">
    <div class="thumb" role="img" aria-label="Hands holding glowing digital interface icons" style="background:linear-gradient(135deg,#0b2a5c,#2a6fb8 55%,#0a1a3a)"></div>
    <div class="card">
      <div class="meta">30 MAY 2024 &nbsp;/&nbsp; MARA LIND</div>
      <h3>Lorem ipsum dolor sit amet, consectetur elit,</h3>
      <p>Sed ut perspiciatis unde omnis iste natus error sit voluptatem</p>
    </div>
  </article>
  <article class="post featured" style="left:444px">
    <div class="thumb" role="img" aria-label="Team of colleagues looking at a laptop in an office" style="background:linear-gradient(135deg,#2d4a6e,#6f8fb0 50%,#1c2e48)"></div>
    <div class="card">
      <div class="meta" style="color:var(--teal)">30 MAY 2024 &nbsp;/&nbsp; MARA LIND</div>
      <h3>Lorem ipsum dolor sit amet, consectetur elit,</h3>
      <p>Sed ut perspiciatis unde omnis iste natus error sit voluptatem</p>
    </div>
  </article>
  <article class="post" style="left:775px">
    <div class="thumb" role="img" aria-label="Engineer at a workstation with a glowing cloud graphic" style="background:linear-gradient(135deg,#1a2440,#8a4a4a 55%,#1d2a48)"></div>
    <div class="card">
      <div class="meta">30 MAY 2024 &nbsp;/&nbsp; MARA LIND</div>
      <h3>Lorem ipsum dolor sit amet, consectetur elit,</h3>
      <p>Sed ut perspiciatis unde omnis iste natus error sit voluptatem</p>
    </div>
  </article>
</section>

<section class="contact">
  <div class="contact-panel"></div>
  <div class="contact-heading">
    <div class="eyebrow">CONTACT US</div>
    <div class="headline display">Let’s Do<br>Good<br>Together!</div>
  </div>
  <div class="contact-frame"></div>
  <form class="form-card">
    <h2 class="section-title">Send Us a Message</h2>
    <div class="rule"></div>
    <div class="field" style="left:57px;top:117px"><label>Your Name</label><span>Alex Rowan</span></div>
    <div class="field" style="left:333px;top:117px"><label>Company</label><span>Lorem ipsum dolor sit amet</span></div>
    <div class="field" style="left:57px;top:210px"><label>Email Address</label><span>alex.rowan@mail.com</span></div>
    <div class="field" style="left:333px;top:210px"><label>Phone</label><span>01234-555-010-200</span></div>
    <div class="field wide" style="left:57px;top:302px"><label>Message</label><span style="padding-bottom:22px">Hi, do you have a moment to talk abo...|</span></div>
    <div class="send">
      <svg width="24" height="24" viewBox="0 0 24 24"><path d="M3 12L21 4l-5 17-4-7z" fill="#fff"/></svg>
    </div>
  </form>
</section>

<footer>
  <svg class="footer-shape" width="1200" height="395" viewBox="0 0 1200 395" aria-hidden="true">
    <polygon points="0,155 600,45 1200,155 1200,395 0,395" fill="var(--ink)"/>
    <polygon points="103,140 600,30 1097,140 1097,162 600,52 103,162" fill="var(--cyan)"/>
  </svg>
  <div class="brand footer-brand">
    <span class="brand-dot"></span><span class="brand-name" style="color:var(--white)">VORTEQ</span>
  </div>
  <div class="footer-col" style="left:423px">
    <h5>QUICK LINKS</h5><div class="rule"></div>
    <ul class="links"><li>Home</li><li>About Us</li><li>Products</li><li>Blog</li><li>Contact Us</li></ul>
  </div>
  <div class="footer-col" style="left:592px">
    <h5>CONTACT US</h5><div class="rule"></div>
    <div class="contact-line"><span class="ic"><svg width="12" height="12" viewBox="0 0 12 12"><path d="M2 1l2 0 1 3-1.5 1a7 7 0 003.5 3.5L8 7l3 1v2c0 .6-.4 1-1 1A9 9 0 011 2c0-.6.4-1 1-1z" fill="#0f9e97"/></svg></span>(555) 210-4780</div>
    <div class="contact-line"><span class="ic"><svg width="12" height="12" viewBox="0 0 12 12"><rect x="1" y="2.5" width="10" height="7" rx="1" fill="#0f9e97"/><path d="M1.5 3l4.5 3.5L10.5 3" stroke="#fff" fill="none"/></svg></span>hello@vorteq.org</div>
    <div class="contact-line"><span class="ic"><svg width="12" height="12" viewBox="0 0 12 12"><path d="M6 11S2 7 2 4.5a4 4 0 018 0C10 7 6 11 6 11z" fill="#0f9e97"/><circle cx="6" cy="4.5" r="1.4" fill="#fff"/></svg></span>22 Harbor Lane, Suite 4,<br>Brookfield, CT 06804</div>
    <div class="contact-line"><span class="ic"><svg width="12" height="12" viewBox="0 0 12 12"><rect x="1.5" y="2" width="9" height="8" rx="1" fill="#0f9e97"/></svg></span>(555) 318-662</div>
  </div>
  <div class="footer-col subscribe" style="left:832px">
    <h5>SUBSCRIBE TO OUR BLOG</h5><div class="rule"></div>
    <p>Sign up today to get resources on how to attract and retain more customers!</p>
    <div class="sub-form"><div class="input">✉ Email Address</div><div class="go"><svg width="16" height="16" viewBox="0 0 24 24"><path d="M3 12L21 4l-5 17-4-7z" fill="#fff"/></svg></div></div>
    <div class="socials"><span></span><span class="on"></span></div>
  </div>
  <div class="bottom-bar">
    <div class="copy">Copyright© 2025 &nbsp;<b>Vorteq</b> &nbsp;| &nbsp;All Rights Reserved</div>
    <div class="legal">Terms and Conditions &nbsp;&nbsp;| &nbsp;&nbsp;Privacy Policy</div>
  </div>
</footer>

</body>
</html>
```